Operator Qualification Testing Flyer

I have a 8x10 basic flyer that I created usin InDesign for one of our services our company provides. I would like to see more options for the layout and general design of the flyer. This flyer will be used as a template for the other services we provide. I will include the InDesign Folder with all the logos and images. Please feel free to use any logo design within the folder and you can change the font and/or colors as needed. I would like the final output in a Indesign package folder to be used in InDesign 2021

Target Market(s)

Business to Business marketing in the Oil and Gas industry

Font styles to use
Sans Serif

Colors
85cae6
85acd3
3377b5
0355a3
0792cd
ffffff
cedeed

Requirements
Must have
• I included/attached a couple of brochures styles that I do like.

```html
<!DOCTYPE html>
<html lang="en">
<head>
<meta charset="utf-8">
<title>Operator Qualification Testing Flyer</title>
<link rel="stylesheet" href="https://fonts.googleapis.com/css2?family=Arimo:wght@400;700&display=swap">
<style>
  :root {
    --stage: #b5b5b5;
    --paper: #ffffff;
    --band: #3aa3d2;
    --slash-teal: #1b6e86;
    --slash-dark: #222222;
    --ink: #1c1c1c;
    --earth-1: #8a7a68;
    --earth-2: #6b5c4c;
    --sky: #c9d8e6;
    --tundra: #9a4a24;
    --sign-yellow: #f3b21b;
    --sign-dark: #1a1a1a;
  }
  * { margin: 0; padding: 0; box-sizing: border-box; }
  html, body { width: 1200px; height: 1200px; overflow: hidden; background: var(--stage); }
  body { font-family: "Arimo", Arial, sans-serif; color: var(--ink); }

  .flyer {
    position: absolute; left: 190px; top: 20px;
    width: 819px; height: 1160px;
    background: var(--paper); overflow: hidden;
  }
  .hero-photo {
    position: absolute; left: 0; top: 20px; width: 819px; height: 288px;
    background: linear-gradient(135deg, var(--earth-2) 0%, var(--earth-1) 45%, #9b8b77 75%, var(--earth-2) 100%);
  }
  .footer-photo {
    position: absolute; left: 0; top: 960px; width: 819px; height: 178px;
    background: linear-gradient(180deg, #e9eef3 0%, var(--sky) 28%, #8fa4b8 40%, #b0683a 52%, var(--tundra) 75%, #7a3618 100%);
  }
  .sign-photo {
    position: absolute; left: 531px; top: 510px; width: 242px; height: 238px;
    border-radius: 50%;
    background: radial-gradient(circle at 50% 50%, var(--sign-yellow) 0%, var(--sign-yellow) 62%, #d99a12 88%, var(--sign-dark) 92%);
  }

  .section-band {
    position: absolute; left: 0; height: 46px;
  }
  .section-band .band-fill {
    position: absolute; left: 0; top: 0; height: 46px;
    background: var(--band);
  }
  .section-band svg { position: absolute; top: 0; left: 0; }
  .section-title {
    position: absolute; left: 46px; top: 0; line-height: 46px;
    font-weight: 700; font-size: 29px; color: var(--paper); white-space: nowrap;
  }

  .body-copy {
    position: absolute; left: 46px;
    font-size: 16.3px; line-height: 22px; text-align: justify; hyphens: auto;
  }
  .body-copy + .body-copy { margin-top: 0; }
</style>
</head>
<body>
  <main class="flyer">
    <div class="hero-photo" role="img" aria-label="Aerial photo of a pipeline trench with orange safety fencing, green pipe and a yellow pipelayer tractor"></div>

    <div class="section-band" style="top:312px;width:530px;">
      <svg width="530" height="46" viewBox="0 0 530 46">
        <polygon points="0,0 495,0 472,46 0,46" fill="var(--band)"/>
        <polygon points="499,0 508,0 485,46 476,46" fill="var(--slash-teal)"/>
        <polygon points="514,0 528,0 505,46 491,46" fill="var(--slash-dark)"/>
      </svg>
      <h2 class="section-title">What Is Operator Qualification?</h2>
    </div>
    <p class="body-copy" style="top:370px;width:713px;">Operator Qualifications (OQ) for DOT Oil/Gas Pipelines are requirements set by Department of Transportation (DOT) and Pipeline and Hazardous Materials Safety Administration (PHMSA). To assure safety in the transport of hazardous gases and liquids in the nation’s pipelines, pipeline operators who perform covered tasks must be qualified. Qualified means that an individual has been evaluated and can perform assigned covered tasks and recognize and react to abnormal operating conditions.</p>

    <div class="section-band" style="top:544px;width:458px;">
      <svg width="458" height="46" viewBox="0 0 458 46">
        <polygon points="0,0 423,0 400,46 0,46" fill="var(--band)"/>
        <polygon points="427,0 436,0 413,46 404,46" fill="var(--slash-teal)"/>
        <polygon points="442,0 456,0 433,46 419,46" fill="var(--slash-dark)"/>
      </svg>
      <h2 class="section-title">What Are Covered Tasks?</h2>
    </div>
    <p class="body-copy" style="top:603px;width:456px;">Covered tasks are defined in an operator’s written plan which defines specific job functions or activities personnel are qualified to perform on a pipeline facility.</p>

    <div class="sign-photo" role="img" aria-label="Photo of a round yellow pipeline warning marker sign"></div>

    <div class="section-band" style="top:718px;width:350px;">
      <svg width="350" height="46" viewBox="0 0 350 46">
        <polygon points="0,0 315,0 292,46 0,46" fill="var(--band)"/>
        <polygon points="319,0 328,0 305,46 296,46" fill="var(--slash-teal)"/>
        <polygon points="334,0 348,0 325,46 311,46" fill="var(--slash-dark)"/>
      </svg>
      <h2 class="section-title">What We Provide</h2>
    </div>
    <p class="body-copy" style="top:776px;width:713px;">Meridian Field Services Inc. utilizes NTCB pipeline program to administer OQ assessment testing on 127 covered tasks Upon completion of OQ testing the information is first transferred to NTCB’s Registry System and automatically uploaded to SafeLink.</p>
    <p class="body-copy" style="top:861px;width:713px;">In addition to the benefits provided by SafeLink’s database, the NTCB Registry System houses all the completion information allowing candidates to share their training information and employers to verify successful covered task and level completions.</p>

    <div class="footer-photo" role="img" aria-label="Landscape photo of an above-ground pipeline crossing red tundra toward distant mountains"></div>
  </main>
</body>
</html>
```